Corporate Dinner Invite at Corvessa for BRQ

BRQ is hosting a corporate dinner at the VEP Summit and we need an email attachment invite for the event. Please use some images from this site for inspiration: https://www.corvessadining.example/ivyparlor/

Invite Title:
Join us for dinner!

Event Details:
Tuesday, October 24th 2023 at 6:30pm
Corvessa Dining, Ivy Parlor
347 W Marlow Ave, Chicago, IL 60622

Target Market(s)

Corporate Audience

Font styles to use
Script

Colors
0054AA
0677BA
7BADD7
CADEEF
E8F1F8

Requirements
Must have
• BRQ logo, event date / time, event location details, photo(s) from Ivy Parlor

```html
<!DOCTYPE html>
<html lang="en">
<head>
<meta charset="utf-8">
<title>BRQ Dinner Invitation – VEP Summit</title>
<link href="https://fonts.googleapis.com/css2?family=Playball&family=Yellowtail&family=Cormorant+Garamond:ital,wght@1,500;1,600&family=Montserrat:wght@700&display=swap" rel="stylesheet">
<style>
  :root {
    --frame-outer: #3d3f99;
    --frame-inner: #00a9e8;
    --paper: #ffffff;
    --indigo: #3a3d96;
    --sky: #16a6e0;
    --brand: #1f3f88;
  }
  * { margin: 0; padding: 0; box-sizing: border-box; }
  html, body { width: 902px; height: 1200px; overflow: hidden; background: var(--paper); }
  .invite {
    position: relative;
    width: 902px; height: 1200px;
    background: var(--frame-outer);
    padding: 7px;
  }
  .invite__band {
    width: 100%; height: 100%;
    background: var(--frame-inner);
    padding: 29px 22px 30px 22px;
  }
  .invite__card {
    position: relative;
    width: 100%; height: 100%;
    background: var(--paper);
  }
  .brand {
    position: absolute;
    top: 105px; left: 0; right: 0;
    display: flex; justify-content: center; align-items: center; gap: 14px;
  }
  .brand__mark { width: 34px; height: 34px; background: var(--brand); }
  .brand__name {
    font-family: "Montserrat", sans-serif; font-weight: 700;
    font-size: 54px; color: var(--brand); letter-spacing: 2px;
  }
  .title { position: absolute; left: 0; right: 0; text-align: center; }
  .title__lead {
    top: 247px;
    font-family: "Playball", cursive; font-size: 56px; color: var(--sky);
    padding-left: 90px;
  }
  .title__main {
    top: 282px;
    font-family: "Playball", cursive; font-size: 150px; line-height: 1.1;
    color: var(--indigo);
  }
  .photo {
    position: absolute;
    border: 5px solid #fff;
    box-shadow: 0 2px 6px rgba(0,0,0,.25);
  }
  .photo--cocktails {
    left: 68px; top: 458px; width: 272px; height: 180px;
    transform: rotate(8deg);
    background: linear-gradient(160deg, #3a2416 0%, #7a4a22 45%, #d9b070 75%, #e9e1d8 100%);
  }
  .photo--dining {
    left: 290px; top: 470px; width: 272px; height: 180px;
    transform: rotate(9deg);
    background: linear-gradient(170deg, #4a3526 0%, #6e5342 40%, #c9b8a4 80%, #8c7060 100%);
  }
  .photo--bar {
    left: 485px; top: 480px; width: 300px; height: 190px;
    transform: rotate(8deg);
    background: linear-gradient(165deg, #2b211b 0%, #5a4330 45%, #b08548 70%, #3a2a20 100%);
  }
  .venue-tag {
    position: absolute; top: 738px; left: 0; right: 0; text-align: center;
    font-family: "Playball", cursive; font-size: 42px; color: var(--sky);
  }
  .venue-tag__at { font-size: 24px; }
  .details {
    position: absolute; top: 808px; left: 0; width: 100%;
    font-family: "Cormorant Garamond", serif; font-style: italic; font-weight: 600;
    color: var(--indigo); font-size: 37px; line-height: 1.15;
  }
  .details__row { position: relative; padding-left: 214px; margin-bottom: 10px; }
  .details__row--address { margin-bottom: 0; }
  .details__icon { position: absolute; left: 160px; top: 10px; width: 34px; height: 34px; }
  .details__sub { display: block; }
  .signoff {
    position: absolute; top: 1010px; left: 0; right: 0; text-align: center;
    font-family: "Yellowtail", cursive; font-size: 84px; color: var(--sky);
  }
</style>
</head>
<body>
<main class="invite">
  <div class="invite__band">
    <div class="invite__card">
      <div class="brand">
        <span class="brand__mark"></span>
        <span class="brand__name">BRQ</span>
      </div>

      <p class="title title__lead">Join us for</p>
      <h1 class="title title__main">Dinner</h1>

      <div class="photo photo--cocktails" role="img" aria-label="Photo of signature cocktails lined up on the Ivy Parlor bar"></div>
      <div class="photo photo--dining" role="img" aria-label="Photo of the Ivy Parlor dining room with arched windows and set tables"></div>
      <div class="photo photo--bar" role="img" aria-label="Photo of the warmly lit Ivy Parlor lounge bar"></div>

      <p class="venue-tag"><span class="venue-tag__at">@</span> VEP Summit</p>

      <div class="details">
        <p class="details__row">
          <svg class="details__icon" viewBox="0 0 34 34" aria-hidden="true">
            <rect x="2" y="5" width="30" height="27" fill="#16a6e0"/>
            <rect x="8" y="1" width="3" height="7" fill="#16a6e0"/>
            <rect x="23" y="1" width="3" height="7" fill="#16a6e0"/>
            <g fill="#fff">
              <rect x="5" y="12" width="4" height="3"/><rect x="11" y="12" width="4" height="3"/><rect x="17" y="12" width="4" height="3"/><rect x="23" y="12" width="4" height="3"/>
              <rect x="5" y="18" width="4" height="3"/><rect x="11" y="18" width="4" height="3"/><rect x="17" y="18" width="4" height="3"/><rect x="23" y="18" width="4" height="3"/>
              <rect x="5" y="24" width="4" height="3"/><rect x="11" y="24" width="4" height="3"/><rect x="17" y="24" width="4" height="3"/><rect x="23" y="24" width="4" height="3"/>
            </g>
          </svg>
          Tuesday, October 24th, 2023
        </p>
        <p class="details__row">
          <svg class="details__icon" viewBox="0 0 34 34" aria-hidden="true">
            <circle cx="17" cy="17" r="14" fill="none" stroke="#16a6e0" stroke-width="3"/>
            <path d="M17 8v9l7 5" fill="none" stroke="#16a6e0" stroke-width="3" stroke-linecap="round"/>
          </svg>
          6:30pm
        </p>
        <p class="details__row details__row--address">
          <svg class="details__icon" viewBox="0 0 34 34" aria-hidden="true">
            <circle cx="17" cy="17" r="14" fill="none" stroke="#16a6e0" stroke-width="3"/>
            <path d="M17 27c-5-6-7-9-7-12a7 7 0 0 1 14 0c0 3-2 6-7 12z" fill="none" stroke="#16a6e0" stroke-width="2.5"/>
            <circle cx="17" cy="15" r="2.5" fill="#16a6e0"/>
          </svg>
          Corvessa Dining, Ivy Parlor
          <span class="details__sub">347 W Marlow Ave, Chicago, IL 60622</span>
        </p>
      </div>

      <p class="signoff">See You There!</p>
    </div>
  </div>
</main>
</body>
</html>
```